Web Design Project

Psychotherapy and Counselling Practice needs a landing page web design.

My business "Larkfield Advisory" specialises in the treatment of Anxiety and Depression with a holistic approach, endeavouring to unlock the key that holds us to ransom in a life that is imbalanced, frustrating, and ultimately of our own making due to our own perceptions and behaviours.

There is much that impacts us which we cannot change, but we are always in control of how we think, and how we frame our experiences.....learning to challenge those thoughts and behaviours that are destructive and disempowering opens up a world of joyful possibility. Life is about making choices, learn to make wiser and healthier choices.......

Larkfield Advisory has a client base of individual clients but will seek to expand to offer services to the Corporate world by offering an adjunct to employers for established "Wellness Programs".

Larkfield Advisory is a highly professional, ethically bound business, with the needs of the client at the forefront of all we do.

Larkfield Advisory wishes to avoid the usual "jargon driven" psychobabble offered on many counselling web pages. It aims to be stylishly presented, clean in look and with as few "words" as possible and a largely white background (faster loading and more powerful impact of what is stated), those words contained in the webpage should be meaningful, persuasive and have an impact simply at glance. Larkfield does not want , or expect, those prospective clients in need of support , to be reading through volumes of industry driven cliches.

At this point Larkfield is just looking for a high quality landing page. However in time this will likely expand to include other sections such as case studies, video content etc.

Target Market(s)

Those in need of emotional support, suffering mental health issues, and those simply wanting to become self aware supported by a mindful therapist.

Industry/Entity Type

Industry

Requirements
Must have
• The design must incorporate the Larkfield logo and colour schemes found on the attached files.

```html
<!DOCTYPE html>
<html lang="en">
<head>
<meta charset="utf-8">
<title>Larkfield Advisory</title>
<link href="https://fonts.googleapis.com/css2?family=Roboto:wght@300;400;500&display=swap" rel="stylesheet">
<style>
:root{
  --green:#8aaa0c;
  --green-light:#b5d925;
  --green-text:#7e9f06;
  --grey-dark:#555455;
  --grey-mid:#7b7b7b;
  --text:#666;
  --white:#fff;
}
*{margin:0;padding:0;box-sizing:border-box}
html,body{width:1133px;height:1200px;overflow:hidden;background:var(--white)}
body{position:relative;font-family:"Roboto",Arial,sans-serif;color:var(--text)}
.abs{position:absolute}
.brand{left:113px;top:80px;display:flex;align-items:center;gap:8px;font-weight:300;font-size:26px;letter-spacing:1px;color:var(--green)}
.brand-mark{width:10px;height:10px;background:var(--green)}
.contact{right:113px;top:37px;text-align:right}
.contact .phone{font-size:20px;color:var(--green);font-weight:400}
.contact .email{font-size:13.5px;color:var(--grey-dark);margin-top:6px;letter-spacing:.3px}
.search{left:767px;top:107px;width:252px;height:35px;border:1px solid #e2e2e2;background:var(--white)}
.search-btn{position:absolute;right:2px;top:2px;width:35px;height:29px;background:linear-gradient(#9cc21a,#6f8d06)}
.wave{left:0;top:150px;width:1133px;height:60px}
.band{left:0;top:198px;width:1133px;height:447px;background:var(--green)}
.nav a{position:absolute;top:210px;height:36px;line-height:36px;color:var(--white);font-size:15.5px;text-decoration:none}
.nav .active{left:112px;width:98px;text-align:center;background:var(--grey-mid)}
.slide{left:113px;top:261px;width:906px;height:340px;background:var(--white);padding:10px;box-shadow:0 12px 14px -8px rgba(0,0,0,.35)}
.slide-photo{width:100%;height:100%;background:linear-gradient(100deg,#0d2a10 0%,#24501c 30%,#6a7a3a 48%,#c99a72 62%,#e7d2c3 80%,#f3f0ee 100%);position:relative}
.slide-title{position:absolute;left:18px;top:168px;font-size:29.5px;line-height:34px;color:var(--white);font-weight:400}
.slide-title span{color:var(--green-light)}
.dots{left:533px;top:621px;display:flex;gap:5px}
.dots i{width:9px;height:9px;border-radius:50%;background:#9a9a9a;border:1px solid #d0d0d0}
.dots i.on{background:#a7bf3b}
.card{top:664px;width:283px}
.card-photo{height:132px}
.card-label{height:36px;background:var(--grey-dark);color:var(--white);font-size:17.5px;line-height:38px;padding-left:8px;letter-spacing:.3px}
.col{top:860px;width:283px}
.col h2{font-size:15.5px;font-weight:400;color:var(--grey-dark);padding-bottom:8px;border-bottom:3px solid var(--green);letter-spacing:.2px}
.col h2 span{color:var(--green-text)}
.col p{font-size:11.3px;line-height:17px;text-align:justify;font-weight:300;color:#555;margin-top:14px}
.col p.lead{color:var(--green-text)}
.col p+p{margin-top:17px}
.more{top:1079px;width:66px;height:27px;background:var(--grey-mid);color:var(--white);font-size:9.5px;line-height:27px;text-align:center;letter-spacing:.3px}
.footer{left:0;top:1133px;width:1133px;height:67px;background:var(--grey-dark)}
.copy{left:113px;top:1161px;color:var(--white);font-size:11.5px;font-weight:300}
.social{left:891px;top:1149px;display:flex;gap:8px}
.social i{width:26px;height:26px;border-radius:50%}
</style>
</head>
<body>
<div class="abs brand"><span class="brand-mark"></span>LARKFIELD</div>
<div class="abs contact">
  <div class="phone">CALL US : (000) 000 000</div>
  <div class="email">EMAIL:INFO@LARKFIELDMAIL.COM</div>
</div>
<div class="abs search"><div class="search-btn">
  <svg width="35" height="29" viewBox="0 0 35 29"><circle cx="15" cy="12" r="4" fill="none" stroke="#fff" stroke-width="2"/><line x1="18" y1="15" x2="23" y2="19" stroke="#fff" stroke-width="2.5"/></svg>
</div></div>

<svg class="abs wave" viewBox="0 0 1133 60" preserveAspectRatio="none">
  <path d="M0 12 C120 5 250 28 450 24 C700 20 950 70 1133 24 L1133 60 L0 60 Z" fill="#8aaa0c"/>
  <path d="M0 26 C150 18 300 34 450 24" fill="none" stroke="#fff" stroke-width="3"/>
</svg>
<div class="abs band"></div>

<nav class="nav">
  <a class="active">HOME</a>
  <a style="left:241px">ABOUT US</a>
  <a style="left:374px">SERVICES</a>
  <a style="left:503px">RESOURCES</a>
  <a style="left:646px">MEDIA</a>
  <a style="left:751px">CONSULTING</a>
  <a style="left:902px">CONTACT US</a>
</nav>

<div class="abs slide">
  <div class="slide-photo" role="img" aria-label="Close-up of a person meditating cross-legged outdoors">
    <div class="slide-title">WE CONDUCT<br><span>WELLNESS PROGRAMS</span></div>
  </div>
</div>
<div class="abs dots"><i></i><i></i><i class="on"></i><i></i><i></i></div>

<div class="abs card" style="left:113px">
  <div class="card-photo" role="img" aria-label="Worried young woman resting her head on her hand" style="background:linear-gradient(90deg,#e4d2b0,#d8c4a8 40%,#f4f1ee)"></div>
  <div class="card-label">ANXIETY</div>
</div>
<div class="abs card" style="left:425px">
  <div class="card-photo" role="img" aria-label="Young woman sitting hunched against a wall" style="background:linear-gradient(90deg,#c8c8c8,#5a5a5a 45%,#dcdcdc 70%,#cfcfcf)"></div>
  <div class="card-label">DEPRESSION</div>
</div>
<div class="abs card" style="left:736px">
  <div class="card-photo" role="img" aria-label="Woman raising her arms joyfully by the sea" style="background:linear-gradient(#6fa8cf,#8fc0dd 70%,#3f7fa8)"></div>
  <div class="card-label">WELLNESS</div>
</div>

<section class="abs col" style="left:113px">
  <h2>WELCOME TO <span>LARKFIELD</span></h2>
  <p class="lead">Sed ut perspiciatis unde omnis iste natus error sit voluptatem accusantium doloremque laudantium,</p>
  <p>Totam rem aperiam, eaque ipsa quae ab illo inventore veritatis et quasi architecto beatae vitae dicta sunt explicabo. Nemo enim ipsam voluptatem quia voluptas sit aspernatur aut odit aut fugit, sed quia consequuntur magni dolores eos qui ratione voluptatem sequi nesciunt. Neque porro quisquam est, qui dolorem ipsum quia dolor sit amet,</p>
</section>
<section class="abs col" style="left:425px">
  <h2>OUR <span>SERVICES</span></h2>
  <p>Sed ut perspiciatis unde omnis iste natus error sit voluptatem accusantium doloremque laudantium, Totam rem aperiam, eaque ipsa quae ab illo</p>
  <p>inventore veritatis et quasi architecto beatae vitae dicta sunt explicabo. Nemo enim ipsam voluptatem quia voluptas sit aspernatur aut odit aut fugit, sed quia consequuntur magni dolores eos qui ratione voluptatem sequi nesciunt. Neque porro quisquam est, qui dolorem ipsum quia dolor sit amet,</p>
</section>
<section class="abs col" style="left:736px">
  <h2>OUR <span>RESOURCES</span></h2>
  <p>Sed ut perspiciatis unde omnis iste natus error sit voluptatem accusantium doloremque laudantium, Totam rem aperiam, eaque ipsa quae ab illo inventore veritatis et quasi architecto beatae vitae dicta sunt explicabo.</p>
  <p>Nemo enim ipsam voluptatem quia voluptas sit aspernatur aut odit aut fugit, sed quia consequuntur magni dolores eos qui ratione voluptatem sequi nesciunt. Neque porro quisquam est, qui dolorem ipsum quia dolor sit amet,</p>
</section>

<div class="abs more" style="left:113px">MORE INFO</div>
<div class="abs more" style="left:425px">MORE INFO</div>
<div class="abs more" style="left:736px">MORE INFO</div>

<footer class="abs footer"></footer>
<div class="abs copy">© 2013 Larkfield &nbsp;| All Rights Reserved.</div>
<div class="abs social">
  <i style="background:#3b5a9a"></i>
  <i style="background:#2aa3e0"></i>
  <i style="background:#d9261f"></i>
  <i style="background:#f07c1c"></i>
</div>
</body>
</html>
```